Corporate Business Card

Very professional, Modern, Not to busy, include phone address email, website
(253) 617-4930, 18761 52nd Avenue S, Kent, WA 98047, martin@plumlinegroup.com, varkoworks.com

Target Market(s)

Manufacturing

Industry/Entity Type

Aero, machining, manufacturing, Off road racing

Contact Information for Business Card

Phone, address email, website

```html
<!DOCTYPE html>
<html lang="en">
<head>
<meta charset="utf-8">
<title>Varko Works – Business Card</title>
<link rel="stylesheet" href="https://fonts.googleapis.com/css2?family=Montserrat:wght@400;500;700&display=swap">
<style>
  :root {
    --navy: #1b3470;
    --red: #d62632;
    --white: #ffffff;
    --ink: #2b2b2b;
    --grey: #5a5a5a;
    --backdrop: #2a2b2e;
  }
  html, body {
    margin: 0;
    padding: 0;
    width: 1200px;
    height: 947px;
    overflow: hidden;
    background: var(--backdrop);
    font-family: "Montserrat", sans-serif;
  }
  .canvas {
    position: relative;
    width: 1200px;
    height: 947px;
  }
  .card {
    position: absolute;
    left: 240px;
    width: 720px;
    height: 411px;
    border-radius: 22px;
    overflow: hidden;
  }
  .card--front {
    top: 30px;
    background: var(--navy);
    display: flex;
    align-items: center;
    justify-content: center;
  }
  .card--back {
    top: 506px;
    background: var(--white);
  }
  .wordmark {
    font-weight: 700;
    letter-spacing: 1px;
    margin: 0;
  }
  .card--front .wordmark {
    color: var(--white);
    font-size: 64px;
  }
  .card--back .wordmark {
    position: absolute;
    left: 58px;
    top: 178px;
    color: var(--navy);
    font-size: 42px;
  }
  .contact {
    position: absolute;
    left: 400px;
    top: 62px;
    color: var(--ink);
  }
  .contact__name {
    margin: 0;
    color: var(--navy);
    font-weight: 700;
    font-size: 26px;
    line-height: 1.1;
  }
  .contact__title {
    margin: 2px 0 20px;
    color: var(--grey);
    font-weight: 400;
    font-size: 16px;
  }
  .contact__list {
    list-style: none;
    margin: 0;
    padding: 0;
    font-size: 15px;
    line-height: 26px;
  }
  .contact__list li {
    display: flex;
    align-items: center;
    gap: 10px;
  }
  .contact__icon {
    width: 16px;
    height: 16px;
    flex: none;
  }
  .contact__address {
    margin: 8px 0 0 26px;
    font-size: 15px;
    line-height: 22px;
    font-style: normal;
  }
  .card__band {
    position: absolute;
    left: 0;
    bottom: 0;
    width: 720px;
    height: 60px;
  }
</style>
</head>
<body>
<main class="canvas">

  <section class="card card--front" aria-label="Card front">
    <p class="wordmark">Varko Works</p>
  </section>

  <section class="card card--back" aria-label="Card back">
    <p class="wordmark">Varko Works</p>

    <div class="contact">
      <h1 class="contact__name">Adrian Kessler</h1>
      <p class="contact__title">President</p>
      <ul class="contact__list">
        <li>
          <svg class="contact__icon" viewBox="0 0 16 16" aria-hidden="true">
            <circle cx="8" cy="8" r="8" fill="var(--red)"/>
            <path d="M5.2 4.2l1.4-.3.8 1.8-.9.7c.4.9 1.2 1.7 2.1 2.1l.7-.9 1.8.8-.3 1.4c-3 .2-5.8-2.6-5.6-5.6z" fill="#fff"/>
          </svg>
          (253) 617-4930
        </li>
        <li>
          <svg class="contact__icon" viewBox="0 0 16 16" aria-hidden="true">
            <circle cx="8" cy="8" r="8" fill="var(--red)"/>
            <rect x="4" y="5" width="8" height="6" rx="1" fill="#fff"/>
            <path d="M4.3 5.5L8 8.3l3.7-2.8" fill="none" stroke="var(--red)" stroke-width="0.9"/>
          </svg>
          martin@plumlinegroup.com
        </li>
        <li>
          <svg class="contact__icon" viewBox="0 0 16 16" aria-hidden="true">
            <circle cx="8" cy="8" r="8" fill="var(--red)"/>
            <g fill="none" stroke="#fff" stroke-width="0.9">
              <circle cx="8" cy="8" r="4"/>
              <ellipse cx="8" cy="8" rx="1.8" ry="4"/>
              <path d="M4 8h8"/>
            </g>
          </svg>
          www.varkoworks.com
        </li>
      </ul>
      <address class="contact__address">18761 52nd Avenue S<br>Kent, WA 98047</address>
    </div>

    <svg class="card__band" viewBox="0 0 720 60" aria-hidden="true">
      <path d="M0 48 H470 L484 40 Q488 20 500 20 H720 V60 H0 Z" fill="var(--navy)"/>
      <path d="M0 42 H466 L478 34" fill="none" stroke="var(--red)" stroke-width="5"/>
    </svg>
  </section>

</main>
</body>
</html>
```